Occupational Medical Billing and Coding Business needs Postcard

Medical billing and coding business needs marketing postcard to send to target audience of orthopaedic surgeons who practice medicine in California Workers' Compensation industry. These doctors treat injured workers and/or provide medical-legal evaluations and reports for the courts to settle the injured worker's claim. This is a highly specialized area of medical billing and coding. It is extremely complicated and can be very frustrating for doctors and their staff who do not understand the system. I would encourage the designers to check out my website: www.MarlowBrookMedicalBilling.com
I want something bright and colorful that makes bold statements. It has to get their attention. My suggestions for bold statements include:
1) QMEs! Are your bills compliant with DWC's view? We make sure your complexity factors are maximized as well as compliant.
2) We collected over $ 462,000 just in second bill review (SBR) appeals alone and that's just one orthopaedic surgeon! Imagine what we can do for you!

I uploaded a word document with some information about the services I offer. The company logo is also there. Let me know if you need it in another format. The items with the asterisk (**) must be in the postcard.

Thank you so much!

Marlow Brook Medical Billing

Target Market(s)

Orthopaedic Surgeons who treat injured workers in California

Font styles to use
Sans Serif

Colors

Designer to choose colors to be used in the design.

Requirements
Must have
• Expert Billing and Coding Services for:
• QME - AME - IME Evaluations
• Radiology - MRI/CT Scans
• Orthopaedic Surgery
• Certified Coders on Staff
• Electronic Claim Submission
• Payment within 15 days
• It's important to spell orthopaedic with the "A" after the "P" as it is an acknowledgment of the origins of the practice and will attract a doctor with higher education.

```html
<!DOCTYPE html>
<html lang="en">
<head>
<meta charset="utf-8">
<title>Marlow Brook Medical Billing – Postcard</title>
<link rel="stylesheet" href="https://fonts.googleapis.com/css2?family=Open+Sans:wght@400;600;700;800&display=swap">
<style>
  :root{
    --blue:#1b87cf;
    --blue-dark:#0f5f9e;
    --navy:#143f6b;
    --peach:#f8cfae;
    --peach-soft:#fbe3cf;
    --white:#ffffff;
    --ink:#27323d;
    --line:#b9c2cb;
  }
  *{box-sizing:border-box;margin:0;padding:0}
  html,body{width:1200px;height:2248px;overflow:hidden}
  body{
    background:#dfe2e5;
    font-family:"Open Sans",Arial,sans-serif;
    color:var(--ink);
    display:flex;flex-direction:column;align-items:center;justify-content:center;gap:90px;
  }
  .card{position:relative;width:1100px;height:730px;background:var(--white);overflow:hidden;box-shadow:0 6px 18px rgba(0,0,0,.18)}
  .abs{position:absolute}

  /* front */
  .front-header{left:0;top:0;width:1100px;height:165px;background:var(--peach)}
  .front-title{left:44px;top:18px;width:720px;font-size:34px;line-height:42px;font-weight:800;color:var(--blue-dark)}
  .brand{right:40px;top:56px;display:flex;align-items:center;gap:12px}
  .brand-mark{width:18px;height:18px;background:var(--blue-dark)}
  .brand-name{font-size:22px;font-weight:600;color:var(--blue-dark);width:190px;line-height:26px}
  .front-photo{left:380px;top:165px;width:720px;height:385px;
    background:linear-gradient(120deg,#f4e6da 0%,#e6bfa3 45%,#d79c7e 70%,#f0dccd 100%)}
  .front-shapes{left:0;top:165px}
  .services{left:40px;top:182px;width:420px;color:var(--white)}
  .services h2{font-size:20px;line-height:26px;font-weight:700;margin-bottom:10px}
  .services ul{list-style:none}
  .services li{display:flex;gap:10px;font-size:16px;line-height:20px;margin-bottom:7px}
  .services li svg{flex:none;margin-top:3px}
  .services li small{display:block;font-size:13px;line-height:18px;opacity:.9}
  .call{left:0;top:550px;width:1100px;height:95px;display:flex;align-items:center;justify-content:flex-end;padding-right:70px;
    font-size:56px;font-weight:700;color:var(--blue)}
  .call-accent{left:0;top:550px;width:360px;height:95px;background:var(--peach-soft)}
  .front-footer{left:0;top:645px;width:1100px;height:85px;background:var(--blue-dark);display:flex;align-items:center;justify-content:space-between;padding:0 44px;color:var(--white);font-size:21px;font-weight:600}
  .contact-item{display:flex;align-items:center;gap:12px}

  /* back */
  .back-shapes{left:0;top:0}
  .back-copy{left:70px;top:60px;width:460px}
  .back-copy h2{font-size:24px;font-weight:800;color:var(--blue-dark);margin-bottom:20px}
  .back-copy ul{padding-left:20px}
  .back-copy li{font-size:15.5px;line-height:22px;margin-bottom:16px}
  .back-contact{left:70px;top:540px;width:440px}
  .back-contact h3{font-size:20px;font-weight:800;color:var(--blue-dark);margin-bottom:8px}
  .back-contact p{font-size:16px;line-height:26px;display:flex;align-items:center;gap:10px}
  .stamp{right:50px;top:50px;width:110px;height:130px;border:2px solid var(--line)}
  .address{left:650px;top:380px;width:400px}
  .address div{height:2px;background:var(--line);margin-bottom:60px}
</style>
</head>
<body>

<section class="card front" aria-label="Postcard front">
  <div class="abs front-header"></div>
  <h1 class="abs front-title">Medical Billing &amp; Collections<br>for California Workers’<br>Compensation Providers</h1>
  <div class="abs brand"><span class="brand-mark"></span><span class="brand-name">Marlow Brook Medical Billing</span></div>

  <div class="abs front-photo" role="img" aria-label="Photo of a knee being wrapped with blue and pink kinesiology tape by a clinician"></div>

  <svg class="abs front-shapes" width="1100" height="385" viewBox="0 0 1100 385">
    <polygon points="0,0 500,0 436,385 0,385" fill="var(--blue)"/>
    <polygon points="500,0 522,0 458,385 436,385" fill="var(--navy)"/>
  </svg>

  <div class="abs services">
    <h2>Expert Billing and Coding Services for:</h2>
    <ul>
      <li><svg width="16" height="14" viewBox="0 0 16 14"><path d="M1 7l5 5L15 1" fill="none" stroke="#fff" stroke-width="2.6"/></svg><span>QME – AME – IME Evaluations<small>Treatment – Primary/Secondary Physician</small></span></li>
      <li><svg width="16" height="14" viewBox="0 0 16 14"><path d="M1 7l5 5L15 1" fill="none" stroke="#fff" stroke-width="2.6"/></svg><span>Radiology – MRI/CT Scans<small>Electrodiagnostic Studies</small></span></li>
      <li><svg width="16" height="14" viewBox="0 0 16 14"><path d="M1 7l5 5L15 1" fill="none" stroke="#fff" stroke-width="2.6"/></svg><span>Orthopaedic Surgery<small>Ambulatory Surgery Centers</small></span></li>
      <li><svg width="16" height="14" viewBox="0 0 16 14"><path d="M1 7l5 5L15 1" fill="none" stroke="#fff" stroke-width="2.6"/></svg><span>Certified Coders on Staff</span></li>
      <li><svg width="16" height="14" viewBox="0 0 16 14"><path d="M1 7l5 5L15 1" fill="none" stroke="#fff" stroke-width="2.6"/></svg><span>Electronic Claim Submission</span></li>
      <li><svg width="16" height="14" viewBox="0 0 16 14"><path d="M1 7l5 5L15 1" fill="none" stroke="#fff" stroke-width="2.6"/></svg><span>Payment within 15 days</span></li>
      <li><svg width="16" height="14" viewBox="0 0 16 14"><path d="M1 7l5 5L15 1" fill="none" stroke="#fff" stroke-width="2.6"/></svg><span>Over 25 Years Experience in<br>Workers’ Comp</span></li>
    </ul>
  </div>

  <div class="abs call-accent"></div>
  <p class="abs call">Call Today:&nbsp; 714.555.0186</p>

  <div class="abs front-footer">
    <span class="contact-item"><svg width="26" height="26" viewBox="0 0 26 26"><circle cx="13" cy="13" r="13" fill="#fff"/><rect x="6" y="8" width="14" height="10" fill="none" stroke="#0f5f9e" stroke-width="2"/><path d="M6 8l7 6 7-6" fill="none" stroke="#0f5f9e" stroke-width="2"/></svg>info@MarlowBrookMedicalBilling.com</span>
    <span class="contact-item"><svg width="26" height="26" viewBox="0 0 26 26"><circle cx="13" cy="13" r="13" fill="#fff"/><circle cx="13" cy="13" r="7" fill="none" stroke="#0f5f9e" stroke-width="2"/><path d="M6 13h14M13 6v14" stroke="#0f5f9e" stroke-width="1.6"/></svg>www.MarlowBrookMedicalBilling.com</span>
  </div>
</section>

<section class="card back" aria-label="Postcard back">
  <svg class="abs back-shapes" width="1100" height="730" viewBox="0 0 1100 730">
    <rect x="0" y="0" width="32" height="730" fill="var(--blue)"/>
    <polygon points="560,0 600,0 540,730 500,730" fill="var(--peach)"/>
    <polygon points="600,0 640,0 580,730 540,730" fill="var(--blue)"/>
    <polygon points="640,0 650,0 590,730 580,730" fill="var(--navy)"/>
    <rect x="32" y="520" width="490" height="3" fill="var(--blue)"/>
  </svg>

  <div class="abs back-copy">
    <h2>We also provide Collection Services:</h2>
    <ul>
      <li>Expert Denial Management: Timely filing of SBR and IBR Appeals – Collected over $462,000 just in second bill review appeals. This is an example of ONE orthopaedic surgeon to date. Imagine what we can do for you!</li>
      <li>Don’t let insurance companies “zero-out” your QME and AME bills. We get your medical-legal bills paid including penalty, interest and costs associated with the effort to collect.</li>
    </ul>
  </div>

  <div class="abs back-contact">
    <h3>Contact Us</h3>
    <p><svg width="16" height="16" viewBox="0 0 16 16"><path d="M3 1l3 3-2 2c1 2 3 4 5 5l2-2 3 3-2 3C7 15 1 9 1 3z" fill="#1b87cf"/></svg>714.555.0186</p>
    <p><svg width="16" height="16" viewBox="0 0 16 16"><rect x="1" y="3" width="14" height="10" fill="none" stroke="#1b87cf" stroke-width="2"/><path d="M1 3l7 6 7-6" fill="none" stroke="#1b87cf" stroke-width="2"/></svg>info@MarlowBrookMedicalBilling.com</p>
    <p><svg width="16" height="16" viewBox="0 0 16 16"><circle cx="8" cy="8" r="6.5" fill="none" stroke="#1b87cf" stroke-width="2"/><path d="M1.5 8h13M8 1.5v13" stroke="#1b87cf" stroke-width="1.4"/></svg>www.MarlowBrookMedicalBilling.com</p>
  </div>

  <div class="abs stamp"></div>
  <div class="abs address"><div></div><div></div><div></div><div></div></div>
</section>

</body>
</html>
```